Inspiring Fundraising Foundation Website to Provide Academic Scholarships

Hello, we are launching a foundation to provide academic scholarships to high school students for college. We'd like this to be an informational website with contact information. There will be a total of approximately 5-7 pages in all.
The color scheme will be purple and white, with a girly feel. I 've attached the logo for reference!

Target Market(s)

high school students, college students

Industry/Entity Type

Education

Coding

Coded - Design and coding required

Number of Pages Required

5+ page

Font styles to use
Serif
Sans Serif
Script

Colors
6b449b
886aae
b7a5cd
e4daeb
ffffff
fdf9cf
fbf289

Requirements
Must have
• Purple, girly feel, to reflect the logo's style. Should be light-themed
Should not have
• No dark themes (aka heavy on black or dark colors)

```html
<!DOCTYPE html>
<html lang="en">
<head>
<meta charset="utf-8">
<title>Amara Vance Foundation</title>
<link rel="stylesheet" href="https://fonts.googleapis.com/css2?family=Jost:wght@400;500;600;700&family=Open+Sans:wght@400;600&display=swap">
<style>
:root{
  --purple:#6b449b;
  --purple-mid:#886aae;
  --purple-soft:#b7a5cd;
  --lilac:#e4daeb;
  --white:#ffffff;
  --cream:#fdf9cf;
  --yellow:#fbf289;
  --grey-bg:#ebebee;
  --card-bg:#e3e3e6;
  --ink:#2b2b33;
  --text:#55555e;
  --muted:#9a9aa4;
}
*{box-sizing:border-box;margin:0;padding:0}
html,body{width:1200px;height:3922px;overflow:hidden}
body{position:relative;background:var(--white);font-family:"Open Sans",Arial,sans-serif;color:var(--text)}
.abs{position:absolute}
svg.abs{display:block}

/* header */
.brand-name{left:150px;top:26px;width:120px;text-align:center;font-family:"Jost",sans-serif;font-weight:600;color:var(--purple);font-size:30px;line-height:30px}
.brand-name small{display:block;font-size:12px;letter-spacing:4px;line-height:18px}
.call{left:428px;top:26px;display:flex;align-items:center;gap:14px}
.call .dot{width:44px;height:44px;border-radius:50%;background:var(--purple);display:flex;align-items:center;justify-content:center}
.call .label{font-size:11px;color:var(--muted);letter-spacing:1px}
.call .num{font-family:"Jost",sans-serif;font-size:22px;color:var(--purple);line-height:24px}
.follow{left:693px;top:30px}
.follow .label{font-size:11px;color:var(--muted);letter-spacing:1px;margin-bottom:5px}
.socials{display:flex;gap:6px}
.socials span{width:18px;height:18px;display:block;border-radius:2px}
.donate-top{left:910px;top:30px;width:157px;height:42px;background:var(--purple);color:var(--white);font-family:"Jost",sans-serif;font-size:14px;font-weight:500;display:flex;align-items:center;justify-content:center;gap:10px;letter-spacing:.5px}
.nav{left:420px;top:108px;display:flex;font-family:"Jost",sans-serif;font-size:15px;color:var(--ink)}
.nav a{color:inherit;text-decoration:none;padding:4px 14px;margin-right:8px}
.nav a.active{border:1px solid var(--purple);color:var(--purple)}

/* hero */
.hero{left:0;top:160px;width:1200px;height:510px;background:linear-gradient(100deg,#8b7a66 0%,#b9a78f 35%,#6e6a6a 65%,#a89884 100%)}
.hero-tag{left:136px;top:318px;background:var(--purple);color:var(--white);font-size:18px;padding:5px 18px}
.hero-title{left:154px;top:368px;font-family:"Jost",sans-serif;font-weight:600;color:var(--white);font-size:52px;line-height:60px;letter-spacing:2px}
.hero-btn{left:154px;top:500px;width:170px;height:48px;background:var(--yellow);color:var(--ink);font-family:"Jost",sans-serif;font-size:16px;font-weight:500;display:flex;align-items:center;justify-content:center;gap:12px}
.dots{left:545px;top:603px;display:flex;gap:12px}
.dots span{width:11px;height:11px;border-radius:50%;border:2px solid var(--white)}
.dots span.on{background:var(--white)}

/* purple band */
.band{left:0;top:667px;width:1200px;height:230px}
.band-col{top:667px;width:340px;height:210px;padding-top:30px}
.band-col h3{font-family:"Jost",sans-serif;font-size:24px;color:var(--yellow);font-weight:600;margin-bottom:12px}
.band-col p{font-size:12px;color:var(--lilac);line-height:20px;width:270px;margin-bottom:18px}
.band-col .btn{display:inline-block;background:var(--purple-soft);color:var(--white);font-size:12px;padding:8px 16px;font-family:"Jost",sans-serif}
.band-rule{top:667px;width:1px;height:210px;background:var(--purple-mid)}

/* section titles */
.sec-title{left:0;width:1200px;text-align:center;font-family:"Jost",sans-serif;color:var(--purple);font-weight:500;font-size:26px;letter-spacing:1px}
.sec-kicker{left:0;width:1200px;text-align:center;font-family:"Jost",sans-serif;color:var(--purple);font-size:15px;font-weight:600;letter-spacing:1px}
.sec-rule{left:560px;width:80px;height:2px;background:var(--purple-soft)}

/* how it works */
.step{top:1045px;width:300px;text-align:center}
.step .ring{width:190px;height:190px;border-radius:50%;border:2px solid var(--lilac);margin:0 auto 44px;display:flex;align-items:center;justify-content:center;box-shadow:0 4px 10px rgba(107,68,155,.08)}
.step h4{font-family:"Jost",sans-serif;color:var(--purple);font-size:15px;font-weight:600;letter-spacing:.5px;margin-bottom:14px}
.step p{font-size:13px;line-height:22px;color:var(--text);width:280px;margin:0 auto 24px}
.step .more{display:inline-block;border:1px solid var(--purple-soft);color:var(--purple);font-size:11px;font-family:"Jost",sans-serif;padding:5px 14px;letter-spacing:.5px}

/* grey bands */
.grey{left:0;width:1200px;background:var(--grey-bg)}
.edge{left:0;width:1200px;height:24px}

/* why */
.feature{width:400px;display:flex;gap:18px}
.feature .ico{width:30px;flex:none}
.feature h5{font-family:"Jost",sans-serif;color:var(--ink);font-size:16px;font-weight:500;margin-bottom:10px}
.feature p{font-size:12.5px;line-height:22px;color:var(--text);width:290px}
.donate-mid{left:523px;top:2026px;width:177px;height:52px;background:var(--purple);color:var(--white);font-family:"Jost",sans-serif;font-size:18px;font-weight:500;display:flex;align-items:center;justify-content:center;letter-spacing:.5px}

/* news */
.news-card{top:2324px;width:456px;height:240px;background:var(--card-bg)}
.news-card .pic{position:absolute;left:20px;top:26px;width:162px;height:186px}
.news-card .body{position:absolute;left:212px;top:30px;width:220px}
.news-card .date{font-size:10px;color:var(--text);margin-bottom:10px}
.news-card h6{font-family:"Jost",sans-serif;font-size:15px;font-weight:500;color:var(--ink);line-height:22px;margin-bottom:14px}
.news-card p{font-size:12px;line-height:21px;color:var(--text);margin-bottom:10px;text-align:justify}
.news-card .rm{font-size:11px;color:var(--purple);font-family:"Jost",sans-serif;font-weight:600}
.arrow{width:24px;height:40px}

/* testimonials */
.avatar{left:233px;top:2832px;width:114px;height:114px;border-radius:50%;background:radial-gradient(circle at 50% 40%,#d9c8b8,#8a7a70 70%,#c9e6ee 71%)}
.quote-text{left:397px;top:2880px;width:640px;font-size:15px;line-height:26px;color:var(--text)}
.quote-mark{left:394px;top:2812px;font-family:"Jost",sans-serif;font-size:70px;color:#c7c7cd;line-height:70px}
.t-rule{left:397px;top:2975px;width:150px;height:1px;background:#c7c7cd}
.t-name{left:397px;top:2990px;font-size:11px;color:var(--purple);font-weight:600}
.t-name span{color:var(--text);font-weight:400;margin-left:6px}

/* partners */
.partner{background:#c9c9cf}

/* footer */
.foot-name{left:130px;top:3590px;width:190px;text-align:center;font-family:"Jost",sans-serif;font-weight:600;color:var(--purple);font-size:52px;line-height:52px}
.foot-name small{display:block;font-size:16px;letter-spacing:6px;line-height:26px}
.foot-head{font-family:"Jost",sans-serif;font-size:13px;font-weight:600;color:var(--purple);letter-spacing:.5px}
.contact-row{left:410px;display:flex;gap:18px;align-items:flex-start;font-size:12px;line-height:20px;color:var(--text)}
.contact-row .c{width:26px;height:26px;border-radius:50%;background:var(--purple);flex:none;display:flex;align-items:center;justify-content:center}
.input{left:750px;top:3660px;width:317px;height:48px;background:var(--white);border:1px solid #d6d6dc;display:flex;align-items:center;gap:14px;padding-left:22px;font-size:13px;color:var(--text)}
.signup{left:962px;top:3728px;width:105px;height:38px;background:var(--purple);color:var(--white);font-family:"Jost",sans-serif;font-size:15px;font-weight:500;display:flex;align-items:center;justify-content:center}
.foot-rule{left:130px;top:3835px;width:940px;height:1px;background:#d0d0d6}
.copy{right:130px;top:3872px;font-size:11px;color:var(--text)}
</style>
</head>
<body>

<!-- header -->
<div class="abs brand-name">Amara<br>Vance<small>FOUNDATION</small></div>
<div class="abs call">
  <div class="dot"><svg width="20" height="20" viewBox="0 0 24 24"><path fill="#fff" d="M6.6 10.8a15 15 0 0 0 6.6 6.6l2.2-2.2a1 1 0 0 1 1-.25 11.4 11.4 0 0 0 3.6.57 1 1 0 0 1 1 1V20a1 1 0 0 1-1 1A17 17 0 0 1 3 4a1 1 0 0 1 1-1h3.5a1 1 0 0 1 1 1c0 1.25.2 2.45.57 3.57a1 1 0 0 1-.25 1z"/></svg></div>
  <div><div class="label">CALL US</div><div class="num">555.210.4400</div></div>
</div>
<div class="abs follow">
  <div class="label">FOLLOW US</div>
  <div class="socials"><span style="background:#3b5998"></span><span style="background:#1da1f2"></span><span style="background:#0e76a8"></span><span style="background:#e8643a"></span></div>
</div>
<div class="abs donate-top"><svg width="16" height="16" viewBox="0 0 24 24"><path fill="#fff" d="M3 21l4-1 12-12-3-3L4 17zM17 3l4 4 1-1-4-4z"/></svg>DONATE NOW</div>
<nav class="abs nav">
  <a class="active">Home</a><a>About us</a><a>Services</a><a>Fundraise</a><a>Donate</a><a>News &amp; Events</a><a>Contact us</a>
</nav>

<!-- hero -->
<div class="abs hero" role="img" aria-label="Photo of cheerful schoolchildren with backpacks jumping down a school walkway"></div>
<div class="abs hero-tag">There are many variations</div>
<div class="abs hero-title">FUNDRAISING<br>FOUNDATION</div>
<div class="abs hero-btn">LEARN MORE <svg width="8" height="10" viewBox="0 0 8 10"><path d="M0 0l8 5-8 5z" fill="#2b2b33"/></svg></div>
<div class="abs dots"><span class="on"></span><span></span><span class="on"></span><span class="on"></span></div>

<!-- purple band -->
<svg class="abs band" width="1200" height="230" viewBox="0 0 1200 230" preserveAspectRatio="none">
  <polygon fill="#6b449b" points="0,0 1200,0 1200,208 1140,214 1080,207 1020,215 960,209 900,216 840,208 780,214 720,207 660,215 600,209 540,216 480,208 420,214 360,207 300,215 240,209 180,216 120,208 60,214 0,209"/>
</svg>
<div class="abs band-rule" style="left:450px"></div>
<div class="abs band-rule" style="left:790px"></div>
<div class="abs band-col" style="left:131px"><h3>DONATE</h3><p>It is a long established fact that a reader will be distracted by the readable content</p><span class="btn">FIND OUT MORE</span></div>
<div class="abs band-col" style="left:466px"><h3>FUNDRAISE</h3><p>It is a long established fact that a reader will be distracted by the readable content</p><span class="btn">FIND OUT MORE</span></div>
<div class="abs band-col" style="left:822px"><h3>ABOUT US</h3><p>It is a long established fact that a reader will be distracted by the readable content</p><span class="btn">FIND OUT MORE</span></div>

<!-- how it works -->
<div class="abs sec-title" style="top:933px">HOW IT WORKS</div>
<div class="abs sec-rule" style="top:988px"></div>

<div class="abs step" style="left:106px">
  <div class="ring"><svg width="64" height="72" viewBox="0 0 64 72"><g fill="#6b449b"><circle cx="22" cy="8" r="6"/><circle cx="42" cy="8" r="6"/><rect x="14" y="18" width="16" height="28" rx="4"/><rect x="34" y="18" width="16" height="28" rx="4"/><rect x="16" y="44" width="5" height="26"/><rect x="23" y="44" width="5" height="26"/><rect x="36" y="44" width="5" height="26"/><rect x="43" y="44" width="5" height="26"/><rect x="4" y="2" width="4" height="24" transform="rotate(-15 6 14)"/><rect x="56" y="2" width="4" height="24" transform="rotate(15 58 14)"/></g></svg></div>
  <h4>ACHIEVEMENTS</h4>
  <p>There are many variations of passages of Lorem Ipsum available, but the.</p>
  <span class="more">READ MORE</span>
</div>
<div class="abs step" style="left:449px">
  <div class="ring"><svg width="92" height="70" viewBox="0 0 92 70"><g fill="#6b449b"><path d="M46 4L92 24 46 44 0 24z"/><path d="M20 34v18c0 8 12 14 26 14s26-6 26-14V34L46 46z"/><rect x="84" y="24" width="3" height="26"/><circle cx="85.5" cy="52" r="4"/></g></svg></div>
  <h4>SCHOLARSHIPS</h4>
  <p>There are many variations of passages of Lorem Ipsum available, but the.</p>
  <span class="more">READ MORE</span>
</div>
<div class="abs step" style="left:796px">
  <div class="ring"><svg width="60" height="72" viewBox="0 0 60 72"><g fill="none" stroke="#6b449b" stroke-width="3"><path d="M4 4h30l14 14v50H4z"/><path d="M34 4v14h14"/><path d="M12 30h20M12 40h14M12 50h12"/><circle cx="38" cy="46" r="9" fill="#fff"/><path d="M44 53l10 10" stroke-width="5"/></g></svg></div>
  <h4>DISCOVER COLLEGES</h4>
  <p>There are many variations of passages of Lorem Ipsum available, but the.</p>
  <span class="more">READ MORE</span>
</div>

<!-- why choose us -->
<svg class="abs edge" style="top:1448px" width="1200" height="24" viewBox="0 0 1200 24" preserveAspectRatio="none">
  <polygon fill="#ebebee" points="0,14 60,8 120,15 180,9 240,16 300,8 360,14 420,7 480,15 540,9 600,16 660,8 720,14 780,7 840,15 900,9 960,16 1020,8 1080,14 1140,7 1200,13 1200,24 0,24"/>
</svg>
<div class="abs grey" style="top:1471px;height:672px"></div>
<div class="abs sec-kicker" style="top:1527px">WHY CHOOSE US</div>
<div class="abs sec-title" style="top:1553px">AMARA VANCE FOUNDATION</div>
<div class="abs sec-rule" style="top:1600px"></div>

<div class="abs feature" style="left:185px;top:1650px">
  <svg class="ico" width="30" height="36" viewBox="0 0 30 36"><g fill="#6b449b"><circle cx="15" cy="13" r="12"/><path d="M7 22l-3 13 6-3 4 4 1-12zM23 22l3 13-6-3-4 4-1-12z"/></g><circle cx="15" cy="13" r="6" fill="#fff"/></svg>
  <div><h5>Best Pricing Guarantee</h5><p>It is a long established fact that a reader will be distracted by the readable content.</p></div>
</div>
<div class="abs feature" style="left:672px;top:1650px">
  <svg class="ico" width="30" height="30" viewBox="0 0 30 30"><circle cx="15" cy="15" r="10" fill="none" stroke="#6b449b" stroke-width="3" stroke-dasharray="4 2.5"/><circle cx="15" cy="15" r="4" fill="none" stroke="#6b449b" stroke-width="2"/></svg>
  <div><h5>No Goal Requirements</h5><p>It is a long established fact that a reader will be distracted by the readable content.</p></div>
</div>
<div class="abs feature" style="left:185px;top:1778px">
  <svg class="ico" width="30" height="34" viewBox="0 0 30 34"><path d="M15 2l12 5v10c0 8-6 13-12 15C9 30 3 25 3 17V7z" fill="#6b449b"/><path d="M9 17l4 4 8-8" stroke="#fff" stroke-width="3" fill="none"/></svg>
  <div><h5>Most Trusted</h5><p>It is a long established fact that a reader will be distracted by the readable content.</p></div>
</div>
<div class="abs feature" style="left:672px;top:1778px">
  <svg class="ico" width="30" height="30" viewBox="0 0 30 30"><g fill="none" stroke="#6b449b" stroke-width="3"><circle cx="14" cy="16" r="11"/><circle cx="14" cy="16" r="5"/><path d="M14 16L27 3"/></g></svg>
  <div><h5>Our Mission</h5><p>It is a long established fact that a reader will be distracted by the readable content.</p></div>
</div>
<div class="abs feature" style="left:185px;top:1906px">
  <svg class="ico" width="30" height="34" viewBox="0 0 30 34"><g fill="#6b449b"><path d="M3 8L15 3l12 5-12 5z"/><circle cx="15" cy="15" r="6"/><path d="M3 33c0-8 5-11 12-11s12 3 12 11z"/></g></svg>
  <div><h5>High School Students</h5><p>It is a long established fact that a reader will be distracted by the readable content.</p></div>
</div>
<div class="abs feature" style="left:672px;top:1906px">
  <svg class="ico" width="30" height="32" viewBox="0 0 30 32"><g fill="none" stroke="#6b449b" stroke-width="3"><path d="M4 18v-3a11 11 0 0 1 22 0v3"/><path d="M24 24c0 4-4 6-8 6"/></g><g fill="#6b449b"><rect x="1" y="16" width="7" height="10" rx="2"/><rect x="22" y="16" width="7" height="10" rx="2"/></g></svg>
  <div><h5>Get Support</h5><p>It is a long established fact that a reader will be distracted by the readable content.</p></div>
</div>
<div class="abs donate-mid">DONATE NOW</div>

<!-- latest news -->
<div class="abs sec-kicker" style="top:2198px">THERE ARE MANY</div>
<div class="abs sec-title" style="top:2222px">LATEST NEWS</div>
<div class="abs sec-rule" style="top:2275px"></div>
<svg class="abs arrow" style="left:68px;top:2420px" viewBox="0 0 24 40"><path d="M18 6L6 20l12 14" stroke="#b8b8bf" stroke-width="3" fill="none"/></svg>
<svg class="abs arrow" style="left:1100px;top:2420px" viewBox="0 0 24 40"><path d="M6 6l12 14L6 34" stroke="#b8b8bf" stroke-width="3" fill="none"/></svg>
<div class="abs news-card" style="left:131px">
  <div class="pic" role="img" aria-label="Photo of a teacher with pupils at desks in a classroom" style="background:linear-gradient(135deg,#6b7a5c,#c9b79a 55%,#8a6a4e)"></div>
  <div class="body"><div class="date">17 Feb,2017</div><h6>IT IS A LONG ESTABLISHED THAT A READER WILL BE</h6><p>There are many variations of passages of Lorem Ipsum available, but the majority have .</p><div class="rm">READ MORE ▸</div></div>
</div>
<div class="abs news-card" style="left:614px">
  <div class="pic" role="img" aria-label="Photo of smiling students celebrating together" style="background:linear-gradient(135deg,#b7c6d6,#c9574f 50%,#3d4b7a)"></div>
  <div class="body"><div class="date">17 Feb,2017</div><h6>THERE ARE MANY VARIATIONS OF PASSAGES OF LOREM</h6><p>At vero eos et accusamus et iusto odio dignissimos ducimus qui blanditiis praesentium.</p><div class="rm">READ MORE ▸</div></div>
</div>

<!-- testimonials -->
<svg class="abs edge" style="top:2626px" width="1200" height="24" viewBox="0 0 1200 24" preserveAspectRatio="none">
  <polygon fill="#ebebee" points="0,12 60,7 120,15 180,8 240,14 300,9 360,16 420,8 480,14 540,7 600,15 660,9 720,16 780,8 840,14 900,7 960,15 1020,9 1080,16 1140,8 1200,14 1200,24 0,24"/>
</svg>
<div class="abs grey" style="top:2649px;height:423px"></div>
<div class="abs sec-kicker" style="top:2696px">WHAT ARE CUSTOMER SAYING</div>
<div class="abs sec-title" style="top:2720px">OUR TESTIMONIALS</div>
<div class="abs sec-rule" style="top:2773px"></div>
<svg class="abs arrow" style="left:130px;top:2868px" viewBox="0 0 24 40"><path d="M18 6L6 20l12 14" stroke="#b8b8bf" stroke-width="3" fill="none"/></svg>
<svg class="abs arrow" style="left:1040px;top:2868px" viewBox="0 0 24 40"><path d="M6 6l12 14L6 34" stroke="#b8b8bf" stroke-width="3" fill="none"/></svg>
<div class="abs avatar" role="img" aria-label="Portrait photo of the reviewer"></div>
<div class="abs quote-mark">“</div>
<div class="abs quote-text">On the other hand, we denounce with righteous indignation and dislike men who are so beguiled and demoralized by the charms of pleasure of the moment, so blinded by desire that they cannot foresee the pain and trouble that.</div>
<div class="abs t-rule"></div>
<div class="abs t-name">MARCUS HALE<span>Explorer</span></div>

<!-- partners -->
<div class="abs sec-kicker" style="top:3128px">SOME OF OUR</div>
<div class="abs sec-title" style="top:3156px">200+ COLLEGE PARTNERS</div>
<div class="abs sec-rule" style="top:3208px"></div>
<div class="abs partner" style="left:192px;top:3280px;width:60px;height:56px;border-radius:50%"></div>
<div class="abs partner" style="left:340px;top:3292px;width:125px;height:26px"></div>
<div class="abs partner" style="left:545px;top:3276px;width:60px;height:60px;border-radius:50%"></div>
<div class="abs partner" style="left:690px;top:3290px;width:132px;height:34px"></div>
<div class="abs partner" style="left:885px;top:3288px;width:165px;height:34px"></div>
<div class="abs partner" style="left:195px;top:3390px;width:54px;height:56px;border-radius:50%"></div>
<div class="abs partner" style="left:330px;top:3408px;width:140px;height:22px"></div>
<div class="abs partner" style="left:545px;top:3386px;width:60px;height:60px;border-radius:50%"></div>
<div class="abs partner" style="left:690px;top:3402px;width:132px;height:30px"></div>
<div class="abs partner" style="left:898px;top:3398px;width:140px;height:36px"></div>

<!-- footer -->
<div class="abs grey" style="top:3524px;height:398px"></div>
<div class="abs foot-name">Amara<br>Vance<small>FOUNDATION</small></div>
<div class="abs foot-head" style="left:410px;top:3586px">CONTACT US</div>
<div class="abs contact-row" style="top:3634px"><span class="c"><svg width="12" height="14" viewBox="0 0 12 14"><path fill="#fff" d="M6 0a5 5 0 0 0-5 5c0 4 5 9 5 9s5-5 5-9a5 5 0 0 0-5-5zm0 7a2 2 0 1 1 0-4 2 2 0 0 1 0 4z"/></svg></span><div>214 Larkspur Avenue<br>Suite 12, Fairview, New York 10420</div></div>
<div class="abs contact-row" style="top:3704px"><span class="c"><svg width="12" height="12" viewBox="0 0 24 24"><path fill="#fff" d="M6.6 10.8a15 15 0 0 0 6.6 6.6l2.2-2.2a1 1 0 0 1 1-.25 11.4 11.4 0 0 0 3.6.57 1 1 0 0 1 1 1V20a1 1 0 0 1-1 1A17 17 0 0 1 3 4a1 1 0 0 1 1-1h3.5a1 1 0 0 1 1 1c0 1.25.2 2.45.57 3.57a1 1 0 0 1-.25 1z"/></svg></span><div style="padding-top:3px">555.210.4400</div></div>
<div class="abs contact-row" style="top:3754px"><span class="c"><svg width="12" height="10" viewBox="0 0 12 10"><rect width="12" height="10" fill="#fff"/><path d="M0 0l6 5 6-5" stroke="#6b449b" fill="none"/></svg></span><div style="padding-top:3px">info@amaravancefoundation.org</div></div>
<div class="abs foot-head" style="left:750px;top:3586px">NEWSLETTER SIGNUP!</div>
<div class="abs" style="left:750px;top:3618px;font-size:12px">Get more details to signup!</div>
<div class="abs input"><svg width="14" height="11" viewBox="0 0 12 10"><rect x=".5" y=".5" width="11" height="9" fill="none" stroke="#55555e"/><path d="M.5.5l5.5 5 5.5-5" stroke="#55555e" fill="none"/></svg>E-mail id</div>
<div class="abs signup">SIGNUP!</div>
<div class="abs foot-rule"></div>
<div class="abs foot-head" style="left:130px;top:3870px;font-size:11px">FOLLOW US</div>
<div class="abs socials" style="left:212px;top:3868px"><span style="background:#3b5998;border-radius:50%"></span><span style="background:#1da1f2;border-radius:50%"></span><span style="background:#e8643a;border-radius:50%"></span></div>
<div class="abs copy">Copyright © 2017 All Rights Reserved</div>

</body>
</html>
```